update of B2B website and conversion to single page

The current website needs to be modernized. I want what is commonly called a single page website. It is not actually a single page. See some examples here:
https://www.plivenor.example/
https://www.quorbel.example/
https://www.trindavex.example/
Most or all graphics will be replaced.
Please see the attached spreadsheet for a rough draft of the home page layout. Convert the existing website at https://www.zolvarin.example/ to a single page website. We will provide the page content. You will provide all of the design, graphics, development, production deployment. etc. The look and feel should be corporate, polished, premium.

```html
<!DOCTYPE html>
<html lang="en">
<head>
<meta charset="utf-8">
<title>Zolvarin – Enterprise Data Quality Made Easy</title>
<link rel="stylesheet" href="https://fonts.googleapis.com/css2?family=Mulish:wght@400;600;700;800&display=swap">
<style>
:root{
  --navy:#1a1f5c;
  --navy-deep:#121641;
  --navy-dark:#0d1033;
  --gold:#f5b516;
  --gold-soft:#fbc531;
  --white:#ffffff;
  --ink:#2b2b3a;
  --muted:#8a8d9c;
  --light:#f2f3f6;
}
*{box-sizing:border-box;margin:0;padding:0}
html,body{width:1200px;height:3340px;overflow:hidden}
body{position:relative;font-family:"Mulish",sans-serif;color:var(--ink);background:var(--white)}
.abs{position:absolute}
.topbar{left:0;top:0;width:1200px;height:32px;background:var(--navy-deep);color:var(--white);font-size:12px;text-align:right;padding:9px 115px 0 0}
.header{left:0;top:32px;width:1200px;height:98px;background:var(--white)}
.brand{left:112px;top:22px;display:flex;align-items:center;gap:12px}
.brand-dot{width:38px;height:38px;border-radius:50%;background:var(--gold)}
.brand-name{font-size:30px;font-weight:700;color:var(--navy)}
.brand-tag{left:162px;top:66px;font-size:11px;color:var(--navy)}
.nav{left:478px;top:42px;display:flex;gap:48px;font-size:16px;color:var(--ink)}
.search{left:1070px;top:42px}
.hero-photo{left:0;top:130px;width:1200px;height:860px;background:linear-gradient(135deg,#2b2f45 0%,#4a4d5e 45%,#6e6a68 70%,#3a3c4c 100%)}
.hero-title{left:0;top:268px;width:1200px;text-align:center;font-size:76px;font-weight:800;color:var(--gold);letter-spacing:1px}
.hero-sub{left:0;top:374px;width:1200px;text-align:center;font-size:19px;color:var(--white)}
.stat{top:459px;width:250px;height:225px;background:var(--white);text-align:center;padding-top:38px;font-size:17px;line-height:29px;color:var(--ink)}
.stat svg{display:block;margin:0 auto 18px}
.dots{left:555px;top:771px;display:flex;gap:8px}
.dots span{width:11px;height:11px;border-radius:50%;border:2px solid var(--white)}
.dots span.on{background:var(--white)}
.marker{font-size:12px}
.marker i{display:block;width:2px;height:70px;margin-top:10px}
.services-bg{left:0;top:900px;width:1200px;height:680px;background:linear-gradient(180deg,#fafbfc,#eef0f3)}
.h2{left:0;width:1200px;text-align:center;font-size:40px;font-weight:700}
.circle{width:430px;height:430px;border-radius:50%;border:6px solid var(--navy);padding:14px;background:var(--white)}
.circle-in{width:100%;height:100%;border-radius:50%;padding:170px 0 0 64px}
.circle h3{font-size:19px;font-weight:800;margin-bottom:14px}
.list{list-style:none;font-size:15px}
.list li{display:flex;align-items:center;gap:16px;height:37px}
.list li::before{content:"";width:12px;height:12px;border-radius:50%;background:var(--gold);box-shadow:inset 0 0 0 3px var(--gold),inset 0 0 0 5px var(--white)}
.dq{background:linear-gradient(160deg,#26306d,#161a4e);color:var(--white)}
.dq h3{color:var(--gold)}
.mdm{background:linear-gradient(160deg,#fbc531,#f2ad0f);color:var(--navy)}
.mdm h3{color:var(--navy)}
.mdm .list li::before{background:var(--navy);box-shadow:inset 0 0 0 3px var(--navy),inset 0 0 0 5px var(--gold)}
.shadow{height:22px;border-radius:50%;background:radial-gradient(ellipse,rgba(0,0,0,.25),transparent 70%)}
.connectors{left:0;top:1560px;width:1200px;height:600px;background:linear-gradient(180deg,var(--gold-soft),var(--gold))}
.conn-card{top:1770px;width:302px;height:274px;background:var(--white);padding:30px 0 0 50px;box-shadow:-6px 6px 0 -2px var(--gold-soft),-8px 8px 0 -2px var(--white)}
.conn-card h3{font-size:17px;font-weight:800;color:var(--navy);margin:0 0 18px 44px;position:relative}
.conn-card h3 svg{position:absolute;left:-48px;top:-8px}
.conn-card .list{font-size:13px}
.conn-card .list li{height:31px}
.soon{color:#b6b8c2}
.support-bg{left:0;top:2150px;width:1200px;height:600px;background:linear-gradient(180deg,#ffffff,#eff1f4)}
.support-title{left:111px;top:2252px;font-size:38px;font-weight:800;color:var(--navy-deep)}
.sup-card{top:2342px;width:305px;height:147px;background:var(--white);border:2px solid var(--gold-soft);box-shadow:-6px 6px 0 -2px var(--white),-8px 8px 0 -2px var(--gold-soft);padding:30px 0 0 126px}
.sup-icon{left:24px;top:30px;width:80px;height:80px;border-radius:50%;background:var(--navy-deep);display:flex;align-items:center;justify-content:center}
.sup-card h4{font-size:16px;font-weight:700;color:var(--navy-deep);margin-bottom:12px}
.sup-card p{font-size:14px;color:var(--muted);line-height:26px}
.contact-title{left:0;top:2770px;width:1200px;text-align:center;font-size:40px;font-weight:800;color:var(--gold)}
.field{height:42px;border:2px solid var(--white);color:var(--white);font-size:13px;padding:11px 0 0 22px}
.submit{left:410px;top:3141px;width:378px;height:45px;background:var(--gold);color:var(--white);font-size:16px;font-weight:700;text-align:center;padding-top:12px;border:0}
.footer{left:0;top:3265px;width:1200px;height:75px;background:var(--navy-dark);color:var(--white);font-size:12px}
.social{left:896px;display:flex;gap:8px}
.social span{width:33px;height:33px;border-radius:50%;background:var(--gold)}
</style>
</head>
<body>

<div class="abs topbar">Phone : (555) 014-2290 &nbsp; | &nbsp; Email : info@zolvarin.example</div>

<header class="abs header">
  <div class="abs brand"><span class="brand-dot"></span><span class="brand-name">Zolvarin</span></div>
  <div class="abs brand-tag">Enterprise Data Quality Made Easy</div>
  <nav class="abs nav"><span>Home</span><span>Services</span><span>Rich Connectors</span><span>Support</span><span>Contact</span></nav>
  <svg class="abs search" width="16" height="16" viewBox="0 0 16 16"><circle cx="6.5" cy="6.5" r="4.8" fill="none" stroke="#f5b516" stroke-width="2"/><path d="M10 10l4.5 4.5" stroke="#f5b516" stroke-width="2.4"/></svg>
</header>

<section>
  <div class="abs hero-photo" role="img" aria-label="Photo of hands working on a tablet with data charts, dark overlay"></div>
  <h1 class="abs hero-title">ZOLVARIN</h1>
  <p class="abs hero-sub">Enterprise Data Quality and Master Data Management Made Easy</p>

  <div class="abs stat" style="left:200px">
    <svg width="66" height="74" viewBox="0 0 66 74"><path d="M33 71C18 52 6 40 6 27a27 27 0 0 1 54 0c0 13-12 25-27 44z" fill="none" stroke="#222" stroke-width="3"/><path d="M33 14v26M20 27h26" stroke="#222" stroke-width="3"/></svg>
    Cleanse addresses<br>in 5 minutes
  </div>
  <div class="abs stat" style="left:474px">
    <svg width="70" height="74" viewBox="0 0 70 74"><circle cx="35" cy="42" r="27" fill="none" stroke="#222" stroke-width="3"/><path d="M29 6h12M35 6v9M35 42V25M35 42l10 8M58 16l5-5" stroke="#222" stroke-width="3"/></svg>
    Match &amp; Merge records<br>in 10 minutes
  </div>
  <div class="abs stat" style="left:750px">
    <svg width="74" height="74" viewBox="0 0 74 74"><rect x="5" y="8" width="64" height="44" fill="none" stroke="#222" stroke-width="3"/><path d="M37 52v12M22 66h30M16 20h8M28 20h28M16 30h8M28 30h28M16 40h8M28 40h20" stroke="#222" stroke-width="3"/></svg>
    Master records in<br>60 minutes
  </div>
  <div class="abs dots"><span class="on"></span><span></span><span></span><span></span><span></span></div>
  <div class="abs marker" style="left:1124px;top:515px;color:var(--gold)">Home<i style="background:var(--gold);margin-left:16px"></i></div>
</section>

<section>
  <div class="abs services-bg" role="img" aria-label="Faint background photo of office desk with charts"></div>
  <svg class="abs" style="left:0;top:730px" width="1200" height="270" viewBox="0 730 1200 270"><path d="M0 980Q600 734 1200 980V1000H0z" fill="#fafbfc"/><path d="M0 980Q600 734 1200 980" fill="none" stroke="#f5b516" stroke-width="5"/></svg>
  <h2 class="abs h2" style="top:953px;color:var(--navy-deep)">OUR SERVICES</h2>

  <div class="abs circle" style="left:108px;top:1038px">
    <div class="circle-in dq" role="img" aria-label="Data quality photo with navy overlay">
      <svg class="abs" style="left:95px;top:75px" width="80" height="80" viewBox="0 0 80 80"><ellipse cx="32" cy="14" rx="24" ry="8" fill="none" stroke="#fff" stroke-width="3"/><path d="M8 14v36c0 4 11 8 24 8M56 14v14M8 26c0 4 11 8 24 8s24-4 24-8M8 38c0 4 11 8 24 8" fill="none" stroke="#fff" stroke-width="3"/><circle cx="54" cy="50" r="14" fill="#1d2360" stroke="#fff" stroke-width="3"/><path d="M54 43l2 5h5l-4 3 2 5-5-3-5 3 2-5-4-3h5z" fill="#f5b516"/><path d="M46 62l-4 14 6-3 4 5 3-12M62 62l4 14-6-3-4 5" fill="none" stroke="#fff" stroke-width="3"/></svg>
      <h3>DATA QUALITY</h3>
      <ul class="list"><li>Global Address Verification</li><li>Data Cleansing/Enrichment</li><li>Match and Merge</li></ul>
    </div>
  </div>
  <div class="abs shadow" style="left:178px;top:1470px;width:290px"></div>

  <div class="abs" style="left:573px;top:1233px;width:50px;height:50px;border-radius:50%;background:var(--gold);border:6px solid var(--navy)"></div>

  <div class="abs circle" style="left:664px;top:1038px">
    <div class="circle-in mdm" role="img" aria-label="Master data management photo with gold overlay">
      <svg class="abs" style="left:95px;top:75px" width="80" height="80" viewBox="0 0 80 80"><path d="M8 72h66M14 72V58h8v14M30 72V48h8v24M46 72V38h8v34M62 72V22h8v50" fill="none" stroke="#1a1f5c" stroke-width="3"/><path d="M6 38l16-14 12 8 22-20M50 12h8v8" fill="none" stroke="#fff" stroke-width="3"/><circle cx="22" cy="24" r="4" fill="#fff"/></svg>
      <h3>MASTER DATA MANAGEMENT</h3>
      <ul class="list"><li>Integration</li><li>Mastering</li><li>Governance</li></ul>
    </div>
  </div>
  <div class="abs shadow" style="left:734px;top:1470px;width:290px"></div>
  <div class="abs marker" style="left:1123px;top:1256px;color:var(--navy)">Services<i style="background:var(--gold);margin-left:23px"></i></div>
</section>

<section>
  <div class="abs connectors" role="img" aria-label="Gold-toned background photo of data reports"></div>
  <svg class="abs" style="left:0;top:2110px" width="1200" height="60" viewBox="0 0 1200 60"><path d="M0 40Q600 -10 1200 40V60H0z" fill="#fff"/><path d="M0 40Q600 -10 1200 40" fill="none" stroke="#1a1f5c" stroke-width="3"/></svg>
  <h2 class="abs h2" style="top:1655px;color:var(--white)">RICH CONNECTORS</h2>
  <div class="abs marker" style="left:8px;top:1809px;color:var(--navy)">Rich Connectors<i style="background:var(--navy);margin-left:44px"></i></div>

  <div class="abs conn-card" style="left:116px">
    <h3><svg width="40" height="40" viewBox="0 0 40 40"><circle cx="20" cy="20" r="7" fill="none" stroke="#1a1f5c" stroke-width="3"/><path d="M20 3v6M20 31v6M3 20h6M31 20h6M8 8l4 4M28 28l4 4M8 32l4-4M28 12l4-4" stroke="#f5b516" stroke-width="4"/><circle cx="20" cy="20" r="13" fill="none" stroke="#1a1f5c" stroke-width="3"/></svg>APPLICATIONS</h3>
    <ul class="list"><li>Trindavex</li><li>Servanta</li><li>Kelbrin</li><li>Orvane Business Suite</li><li class="soon">Maravell Dynamics*</li><li class="soon">Quiltra*</li></ul>
  </div>
  <div class="abs conn-card" style="left:450px">
    <h3><svg width="40" height="40" viewBox="0 0 40 40"><ellipse cx="20" cy="8" rx="14" ry="5" fill="none" stroke="#1a1f5c" stroke-width="3"/><path d="M6 8v24c0 3 6 5 14 5s14-2 14-5V8M6 16c0 3 6 5 14 5s14-2 14-5M6 24c0 3 6 5 14 5s14-2 14-5" fill="none" stroke="#1a1f5c" stroke-width="3"/></svg>DATABASES</h3>
    <ul class="list"><li>Orvane</li><li>Nimbabase</li><li>Maravell Data Hub</li><li>Postara</li><li>Ibrex Vault</li><li class="soon">Terravolt*</li></ul>
  </div>
  <div class="abs conn-card" style="left:784px">
    <h3><svg width="40" height="40" viewBox="0 0 40 40"><rect x="10" y="4" width="24" height="30" fill="#fff" stroke="#1a1f5c" stroke-width="3"/><rect x="5" y="9" width="24" height="30" fill="#fff" stroke="#1a1f5c" stroke-width="3"/><path d="M10 18h14M10 24h14M10 30h10" stroke="#f5b516" stroke-width="3"/></svg>FILES</h3>
    <ul class="list"><li>CSV</li><li>Delimited</li><li>Tabula</li><li>-</li><li>-</li><li class="soon">* Coming Soon</li></ul>
  </div>
</section>

<section>
  <div class="abs support-bg" role="img" aria-label="Faint background photo of hands on a keyboard"></div>
  <h2 class="abs support-title">SUPPORT</h2>
  <div class="abs marker" style="left:1122px;top:2258px;color:var(--navy)">Suport<i style="background:var(--gold);margin-left:18px"></i></div>

  <div class="abs sup-card" style="left:116px">
    <div class="abs sup-icon"><svg width="40" height="40" viewBox="0 0 40 40"><rect x="8" y="6" width="20" height="26" fill="none" stroke="#fff" stroke-width="2.5"/><rect x="13" y="11" width="20" height="26" fill="#121641" stroke="#fff" stroke-width="2.5"/><path d="M18 20h10M18 26h10" stroke="#fff" stroke-width="2"/></svg></div>
    <h4>Batch</h4><p>On your schedule</p>
  </div>
  <div class="abs sup-card" style="left:446px">
    <div class="abs sup-icon"><svg width="44" height="40" viewBox="0 0 44 40"><path d="M17 15l10 5-10 5z" fill="#fff"/><path d="M12 10a14 14 0 0 0 0 20M32 10a14 14 0 0 1 0 20M7 5a21 21 0 0 0 0 30M37 5a21 21 0 0 1 0 30" fill="none" stroke="#fff" stroke-width="2.5"/></svg></div>
    <h4>Streaming</h4><p>Always in sync</p>
  </div>
  <div class="abs sup-card" style="left:776px;padding-top:22px">
    <div class="abs sup-icon"><svg width="40" height="40" viewBox="0 0 40 40"><rect x="6" y="6" width="10" height="10" fill="#fff"/><rect x="24" y="24" width="10" height="10" fill="#fff"/><path d="M11 20v9h9M29 20v-9h-9" fill="none" stroke="#fff" stroke-width="2.5"/></svg></div>
    <h4>Real Time/Interactive</h4><p>Autocomplete Anything<br>Smart Search</p>
  </div>
</section>

<section>
  <svg class="abs" style="left:0;top:2500px" width="1200" height="770" viewBox="0 2500 1200 770"><path d="M0 2515Q600 2845 1200 2515V3270H0z" fill="#1a1f5c"/><path d="M0 2515Q600 2845 1200 2515" fill="none" stroke="#f5b516" stroke-width="6"/></svg>
  <div class="abs marker" style="left:42px;top:2772px;color:var(--gold)">Contact Us<i style="background:var(--gold);margin-left:30px"></i></div>
  <h2 class="abs contact-title">CONTACT US</h2>
  <div class="abs field" style="left:142px;top:2872px;width:450px">Name</div>
  <div class="abs field" style="left:605px;top:2872px;width:450px">Email</div>
  <div class="abs field" style="left:142px;top:2936px;width:450px">Phone</div>
  <div class="abs field" style="left:605px;top:2936px;width:450px">Address</div>
  <div class="abs field" style="left:142px;top:2998px;width:913px;height:112px">Message</div>
  <div class="abs submit">SUBMIT MESSAGE</div>
</section>

<footer class="abs footer">
  <p class="abs" style="left:111px;top:30px">Copyright © Zolvarin. | All rights reserved. &nbsp;| &nbsp;Privacy policy</p>
  <div class="abs social" style="top:21px"><span></span><span></span><span></span><span></span><span></span></div>
</footer>

</body>
</html>
```